Modern 6 page design, business card, and a banner

I need a website design for my CFO service. The service uses proprietary tech, so it needs to be modern. I also need business card and banner design to match the site.
The banner size is 33.75 X 79.25.
I'm open to colors and styles.

Target Market(s)

Startups

Coding

Coded - Design and coding required

Number of Pages Required

5+ page

```html
<!DOCTYPE html>
<html lang="en">
<head>
<meta charset="utf-8">
<title>Tallo — Visual Finance</title>
<link href="https://fonts.googleapis.com/css2?family=Poppins:wght@300;400;500;600;700&display=swap" rel="stylesheet">
<style>
:root{
  --navy:#26234d;
  --navy-deep:#1f1c42;
  --teal:#4fe0b5;
  --ink:#2a2850;
  --text:#3b3a4f;
  --light:#f3f3f7;
  --white:#ffffff;
  --line:#d9d9e3;
}
*{margin:0;padding:0;box-sizing:border-box}
html,body{width:1200px;height:3501px;overflow:hidden}
body{font-family:"Poppins",sans-serif;color:var(--text);background:var(--white);position:relative}
/* nav */
.site-nav{position:absolute;left:0;top:0;width:1200px;height:98px;background:var(--navy)}
.brand{position:absolute;left:111px;top:22px;font-size:40px;font-weight:300;color:var(--white);letter-spacing:1px;line-height:50px}
.menu{position:absolute;left:271px;top:38px;display:flex;gap:38px;list-style:none}
.menu li{font-size:14px;font-weight:500;color:var(--white);letter-spacing:.3px;line-height:20px}
.menu li.active{color:var(--teal);border-bottom:3px solid var(--teal);padding-bottom:5px}
/* hero */
.hero{position:absolute;left:0;top:98px;width:1200px;height:602px;background:linear-gradient(100deg,#4a4d7a 0%,#6f7aa6 40%,#8a94b8 65%,#5b628c 100%)}
.hero::after{content:"";position:absolute;inset:0;background:rgba(38,35,77,.35)}
.hero h1{position:absolute;left:0;right:0;top:170px;text-align:center;z-index:1;color:var(--white);font-size:38px;font-weight:600;line-height:43px}
.btn{display:inline-flex;align-items:center;justify-content:center;font-family:"Poppins",sans-serif;font-weight:600;font-size:15px;border-radius:30px;text-transform:uppercase;letter-spacing:.2px}
.hero .btn{position:absolute;left:521px;top:339px;width:158px;height:58px;background:var(--white);color:var(--navy);z-index:1}
.dots{position:absolute;left:578px;top:542px;display:flex;gap:7px;z-index:1}
.dots span{width:10px;height:10px;border-radius:50%;background:var(--white)}
.dots span:first-child{background:transparent;border:1.5px solid var(--white)}
/* welcome */
.welcome{position:absolute;left:0;top:700px;width:1200px;height:346px;text-align:center}
.welcome h2{margin-top:54px;font-size:35px;font-weight:300;color:var(--ink);letter-spacing:.5px}
.welcome p{width:840px;margin:22px auto 0;font-size:13px;line-height:26.5px;color:var(--text)}
.welcome p+p{margin-top:16px}
/* how it works */
.how{position:absolute;left:0;top:1046px;width:1200px;height:594px;background:var(--light)}
.how-band{position:absolute;left:0;top:288px;width:1200px;height:306px;background:linear-gradient(180deg,#2c2a55,#3a3a68)}
.section-title{font-size:37px;font-weight:700;color:var(--ink);letter-spacing:.3px}
.how h2{position:absolute;left:0;right:0;top:64px;text-align:center}
.how .intro{position:absolute;left:170px;width:860px;top:136px;text-align:center;font-size:13px;line-height:23px}
.steps{position:absolute;left:0;top:232px;width:1200px;height:320px}
.step{position:absolute;width:170px;text-align:center;color:var(--white)}
.step .ring{width:132px;height:132px;margin:0 auto;border-radius:50%;background:var(--white);border:5px solid var(--navy);display:flex;align-items:center;justify-content:center}
.step h3{margin-top:18px;font-size:13px;font-weight:500;letter-spacing:.3px}
.step p{margin-top:6px;font-size:11.5px;line-height:20.5px;color:#e4e4ee}
/* app */
.app{position:absolute;left:0;top:1640px;width:1200px;height:692px}
.app h2{position:absolute;left:111px;top:100px}
.rule{position:absolute;width:66px;height:4px;background:var(--navy)}
.app .copy{position:absolute;left:111px;top:188px;width:520px;font-size:13px;line-height:23.3px}
.app .copy p+p{margin-top:36px}
.btn-solid{background:var(--navy);color:var(--white)}
.app-visual{position:absolute;left:730px;top:37px;width:261px;height:566px;border-radius:36px;background:linear-gradient(180deg,#e9ebf0 0%,#d7dbe6 50%,#e9ebf0 100%)}
/* why */
.why{position:absolute;left:0;top:2332px;width:1200px;height:536px;background:linear-gradient(120deg,#1c2560,#3f6ab3 45%,#28356e)}
.why svg{position:absolute;left:0;top:0}
.why h2{position:absolute;left:720px;top:76px;color:var(--white);font-size:35px;line-height:42px;font-weight:700}
.why .rule{left:720px;top:171px;background:var(--white)}
.why p{position:absolute;left:720px;top:206px;width:330px;color:var(--white);font-size:13px;line-height:26.5px}
/* contact */
.contact{position:absolute;left:0;top:2868px;width:1200px;height:559px;background:#eef0f5}
.contact h2{position:absolute;left:0;right:0;top:64px;text-align:center}
.contact .rule{left:567px;top:122px}
.info{position:absolute;left:111px;list-style:none;font-size:15.5px;color:var(--ink)}
.info li{display:flex;align-items:center;gap:10px;height:47px}
.field{position:absolute;background:var(--white);border:1px solid var(--line);font-size:13.5px;color:#666;padding:12px 13px}
.btn-outline{position:absolute;left:111px;top:422px;width:147px;height:53px;border:2px solid var(--navy);color:var(--navy);font-size:14px}
.contact .submit{position:absolute;left:497px;top:424px;width:143px;height:50px;font-size:14px}
/* footer */
.site-footer{position:absolute;left:0;top:3427px;width:1200px;height:74px;background:var(--navy)}
.site-footer small{position:absolute;left:111px;top:28px;font-size:14px;color:var(--white)}
.social{position:absolute;top:14px;width:46px;height:46px;border-radius:50%;border:2px solid var(--white)}
</style>
</head>
<body>

<header class="site-nav">
  <div class="brand">Tallo</div>
  <ul class="menu">
    <li class="active">HOME</li>
    <li>ABOUT US</li>
    <li>HOW IT WORKS</li>
    <li>TALLO MOBILE APP</li>
    <li>WHY TALLO VISUAL FINANCE</li>
    <li>CONTACT US</li>
  </ul>
</header>

<section class="hero" role="img" aria-label="Photo of a smiling team working at office desks, tinted navy">
  <h1>Tallo combines hands-on financial<br>planning services with real-time<br>mobile monitoring.</h1>
  <span class="btn">Learn More</span>
  <div class="dots"><span></span><span></span><span></span></div>
</section>

<section class="welcome">
  <h2>WELCOME TO TALLO</h2>
  <p>Small businesses can visualize their finances, have a plan they trust and monitor progress daily. No more waiting for the latest monthly or quarterly report from your accountant. No more late nights digging through spreadsheets to figure out where you really stand. No more wondering if you’re prepared for the future.</p>
  <p>Tallo delivers a clear financial plan tailored to your goals, an easy mobile dashboard to track progress on a daily basis and all the professional advice and support you need along the way.</p>
</section>

<section class="how">
  <div class="how-band" role="img" aria-label="Dark navy band with a faint finance chart photo"></div>
  <h2 class="section-title">HOW IT WORKS</h2>
  <p class="intro">Tallo combines traditional bookkeeping and “outsourced CFO” services with a customizable visual finance mobile app. We provide everything needed to develop a plan, clean and structure your accounting data and launch your visual finance dashboard</p>
  <div class="steps">
    <div class="step" style="left:138px">
      <div class="ring"><svg width="56" height="56" viewBox="0 0 56 56" fill="none" stroke="#26234d" stroke-width="2"><path d="M20 50V40c-6-4-9-9-9-16a17 17 0 0 1 34 0l4 8h-4v6a4 4 0 0 1-4 4h-5v8"/><circle cx="27" cy="23" r="7"/><path d="M27 23l4-3"/></svg></div>
      <h3>DEVELOP PLAN</h3>
      <p>We work with you to develop a 3 to 5 year financial plan tailored to your business goals.</p>
    </div>
    <div class="step" style="left:327px">
      <div class="ring"><svg width="56" height="56" viewBox="0 0 56 56" fill="none" stroke="#26234d" stroke-width="2"><ellipse cx="30" cy="30" rx="13" ry="4"/><path d="M17 30v16c0 2 6 4 13 4s13-2 13-4V30"/><path d="M17 37c0 2 6 4 13 4s13-2 13-4M17 43c0 2 6 4 13 4s13-2 13-4"/><path d="M28 26V8h4v18"/></svg></div>
      <h3>CLEAN DATA</h3>
      <p>Our bookkeepers clean your historical data, set-up live data intake, and ensure alignment with finance reports</p>
    </div>
    <div class="step" style="left:514px">
      <div class="ring"><svg width="56" height="56" viewBox="0 0 56 56" fill="none" stroke="#26234d" stroke-width="2"><rect x="14" y="24" width="7" height="12"/><rect x="24" y="16" width="7" height="20"/><rect x="34" y="8" width="7" height="28"/><path d="M6 42h10l8 4h14l12-8M6 50h36l12-10"/></svg></div>
      <h3>VISUAL FINANCES</h3>
      <p>We launch your customized visual finance dashboard on Tallo Mobile</p>
    </div>
    <div class="step" style="left:703px">
      <div class="ring"><svg width="56" height="56" viewBox="0 0 56 56" fill="none" stroke="#26234d" stroke-width="2"><rect x="6" y="10" width="44" height="28"/><path d="M4 10h48M28 38v6M20 52l8-8 8 8M12 32l8-10 8 6 10-12 6 4"/></svg></div>
      <h3>MONITOR DAILY</h3>
      <p>You monitor real financial results against plan on a daily basis</p>
    </div>
    <div class="step" style="left:892px">
      <div class="ring"><svg width="56" height="56" viewBox="0 0 56 56" fill="none" stroke="#26234d" stroke-width="2"><path d="M30 8h20v16h-8l-4 5v-5h-8z"/><path d="M34 14h12M34 19h8"/><circle cx="20" cy="28" r="8"/><path d="M6 50c0-8 6-13 14-13s14 5 14 13"/></svg></div>
      <h3>ADVISE MONTHLY</h3>
      <p>Our financial experts provide support and help respond as your business grows</p>
    </div>
  </div>
</section>

<section class="app">
  <h2 class="section-title">TALLO MOBILE APP</h2>
  <div class="rule" style="left:111px;top:154px"></div>
  <div class="copy">
    <p>Tallo delivers an easy-to-understand dashboard using our own mobile app, customized for your business and your specific plan. Relying on clean data and mirroring your actual financial statements, Tallo lets you see what a CFO sees and always be confident you’re looking at real numbers.</p>
    <p>Monitor results daily, understand where you stand versus plan and make better decisions with Tallo Mobile.</p>
  </div>
  <span class="btn btn-solid" style="position:absolute;left:113px;top:420px;width:172px;height:55px">Learn More</span>
  <div class="app-visual" role="img" aria-label="Product image of a smartphone showing the app's goals dashboard"></div>
</section>

<section class="why">
  <svg width="1200" height="536" viewBox="0 0 1200 536" role="img" aria-label="Photo of a hand touching a glowing heartbeat line on a grid, beside a navy panel">
    <path d="M673 0C565 140 565 396 673 536H1200V0Z" fill="#26234d"/>
  </svg>
  <h2>WHY TALLO<br>VISUAL FINANCE?</h2>
  <div class="rule"></div>
  <p>Small businesses shouldn’t be forced to choose between the strategic value of traditional financial services and the convenience of modern mobile reporting technology. With Tallo, you have access to decades of financial planning experience and a daily view into real finance reports - all delivered through a mobile app you can take with you on the road, in the field, on the shop floor or wherever you need to be.</p>
</section>

<section class="contact">
  <h2 class="section-title">CONTACT US</h2>
  <div class="rule"></div>
  <ul class="info" style="top:228px">
    <li><svg width="14" height="18" viewBox="0 0 14 18"><path d="M7 0a7 7 0 0 0-7 7c0 5 7 11 7 11s7-6 7-11a7 7 0 0 0-7-7z" fill="#26234d"/><circle cx="7" cy="7" r="2.5" fill="#eef0f5"/></svg>Dana Whitfield</li>
    <li><svg width="14" height="14" viewBox="0 0 14 14"><path d="M3 0l3 3-2 2c1 2 3 4 5 5l2-2 3 3-2 3C6 14 0 8 0 3z" fill="#26234d"/></svg>555-014-2280</li>
    <li><svg width="16" height="12" viewBox="0 0 16 12"><rect width="16" height="12" fill="#26234d"/><path d="M0 0l8 7 8-7" fill="none" stroke="#eef0f5" stroke-width="1.5"/></svg>dana.w@example.com</li>
  </ul>
  <div class="field" style="left:497px;top:187px;width:291px;height:38px">Your name</div>
  <div class="field" style="left:796px;top:187px;width:291px;height:38px">Phone number</div>
  <div class="field" style="left:497px;top:247px;width:590px;height:38px">Email</div>
  <div class="field" style="left:497px;top:307px;width:590px;height:90px">Your message</div>
  <span class="btn btn-outline">Learn More</span>
  <span class="btn btn-solid submit">Submit Now</span>
</section>

<footer class="site-footer">
  <small>Copyrights © 2019 Tallo. All rights reserved.</small>
  <span class="social" style="left:940px" aria-label="Social profile"></span>
  <span class="social" style="left:991px" aria-label="Social profile"></span>
  <span class="social" style="left:1042px" aria-label="Social profile"></span>
</footer>

</body>
</html>
```